Website for new crypto research organization

See brief (attached). This is a pretty basic website with only a handful of pages + ability to collect email addresses.

```html
<!DOCTYPE html>
<html lang="en">
<head>
<meta charset="utf-8">
<title>Veltrix Research – Website Pages</title>
<link href="https://fonts.googleapis.com/css2?family=Poppins:wght@400;500;600;700&display=swap" rel="stylesheet">
<style>
:root{
  --board:#18968a;
  --teal:#149e8e;
  --teal-dark:#0d6f66;
  --ink:#1d1d1f;
  --muted:#7a7a7a;
  --line:#e3e3e3;
  --paper:#ffffff;
  --band:#f2f2f2;
  --hero-a:#8d8d8d;
  --hero-b:#b9b3a8;
  --hero-c:#6a7f9c;
  --hero-d:#c26a8d;
  --tech-a:#06262b;
  --tech-b:#0f6a6a;
}
*{box-sizing:border-box;margin:0;padding:0}
html,body{width:674px;height:1200px;overflow:hidden}
body{background:var(--board);font-family:"Poppins",sans-serif;color:var(--ink);position:relative}
.page{position:absolute;background:var(--paper);overflow:hidden;box-shadow:0 2px 6px rgba(0,0,0,.18)}
.home{left:40px;top:24px;width:290px;height:500px}
.about{left:344px;top:24px;width:312px;height:455px}
.careers{left:344px;top:498px;width:312px;height:490px}
.research{left:18px;top:540px;width:312px;height:645px}

.nav{height:16px;display:flex;align-items:center;justify-content:space-between;padding:0 8px;background:var(--paper)}
.logo{color:var(--teal);font-weight:700;font-size:6.5px}
.navlinks{display:flex;gap:7px;font-size:3.4px;color:var(--muted)}
.hero{position:relative;background:
  radial-gradient(circle at 30% 40%,var(--hero-d) 0,transparent 28%),
  radial-gradient(circle at 75% 55%,var(--hero-c) 0,transparent 32%),
  radial-gradient(circle at 55% 30%,var(--hero-b) 0,transparent 40%),
  linear-gradient(120deg,var(--hero-a),#a7a29a 55%,#7d8b8a)}
.hero-title{position:absolute;left:12px;color:var(--paper);font-weight:700;line-height:1.05}
.hero-text{position:absolute;left:12px;color:var(--paper);font-size:3.6px;line-height:1.5;width:120px}

h2{font-weight:600;text-align:center;color:var(--ink)}
.lead{font-size:3.8px;line-height:1.55;color:var(--muted);text-align:center;margin:0 auto}

.footer{position:absolute;left:0;right:0;bottom:0;background:var(--paper);border-top:1px solid var(--line);text-align:center;padding-top:12px}
.footer-links{display:flex;justify-content:center;gap:12px;font-size:3.6px;color:var(--ink)}
.social{display:flex;justify-content:center;gap:5px;margin:7px 0 5px}
.social span{width:5px;height:5px;border-radius:50%;background:var(--ink)}
.copy{font-size:3px;color:var(--muted)}

.services{display:flex;justify-content:center;gap:30px;margin-top:12px}
.service{width:50px;text-align:center;font-size:4px;font-weight:600;line-height:1.3}
.service .dot{width:24px;height:24px;border-radius:50%;background:var(--teal);margin:0 auto 5px;display:flex;align-items:center;justify-content:center}

.newsletter{width:132px;margin:28px auto 0;padding:10px 10px 12px;text-align:center;box-shadow:0 2px 8px rgba(0,0,0,.15);border-top:2px solid var(--teal)}
.newsletter h3{font-size:6px;font-weight:600;color:var(--teal-dark);margin:3px 0 2px}
.newsletter p{font-size:3px;color:var(--muted)}
.subscribe{display:flex;margin-top:6px}
.subscribe .field{flex:1;height:9px;border:1px solid var(--line);font-size:3px;color:var(--muted);text-align:left;padding:2px 3px}
.subscribe .btn{background:var(--teal);color:var(--paper);font-size:3.4px;padding:2.5px 6px}

.team{display:flex;justify-content:center;gap:22px;margin-top:10px}
.member{width:70px;text-align:center}
.portrait{width:42px;height:42px;border-radius:50%;margin:0 auto 5px;background:linear-gradient(160deg,#c9ccd1,#7f8791)}
.member .name{font-size:3.8px;font-weight:600}
.member .role{font-size:3.2px;color:var(--teal)}
.member .bio{font-size:2.9px;color:var(--muted);line-height:1.5;margin-top:3px}

.row{position:absolute;left:20px;right:20px;height:75px}
.tech{position:absolute;width:112px;height:72px;background:radial-gradient(circle at 55% 50%,var(--tech-b),var(--tech-a) 75%)}
.row-text{position:absolute;width:110px}
.row-text h3{font-size:6px;font-weight:600;margin-bottom:4px}
.row-text p{font-size:3px;color:var(--muted);line-height:1.55}

.job{position:absolute;left:22px;top:172px;display:flex;gap:12px}
.job-art{width:100px;height:82px;background:
  radial-gradient(circle at 30% 35%,#d6458a,transparent 40%),
  radial-gradient(circle at 70% 60%,#2f8fd0,transparent 45%),
  radial-gradient(circle at 50% 85%,#f0b43a,transparent 40%),
  linear-gradient(135deg,#4c2f7a,#1e6f83)}
.job-copy{width:155px}
.job-copy h3{font-size:8px;font-weight:600}
.job-copy .sub{font-size:3.4px;color:var(--teal);margin-bottom:4px}
.job-copy p{font-size:3px;color:var(--muted);line-height:1.55;margin-bottom:4px}

.contact{position:absolute;left:0;right:0;top:276px;height:150px;background:var(--band);text-align:center;padding-top:12px}
.form{width:210px;margin:8px auto 0;display:grid;grid-template-columns:1fr 1fr;gap:6px 10px;text-align:left}
.input{font-size:3px;color:var(--muted);border-bottom:1px solid #c9c9c9;padding-bottom:2px}
.input.wide{grid-column:1/3;height:18px}
.submit{display:inline-block;margin-top:8px;background:var(--teal);color:var(--paper);font-size:3.6px;padding:3px 12px}
</style>
</head>
<body>

<!-- Home page -->
<section class="page home">
  <header class="nav"><span class="logo">Veltrix Research</span>
    <nav class="navlinks"><span>Home</span><span>About Us</span><span>Research</span><span>Careers</span><span>News</span><span>Contact</span></nav>
  </header>
  <div class="hero" style="height:150px" role="img" aria-label="Colourful street-art mural of an elephant on a concrete wall"></div>
  <h2 style="font-size:11px;margin-top:14px">Research</h2>
  <p class="lead" style="width:190px;margin-top:4px">We study digital assets with rigorous methods and share findings openly with our growing community of readers.</p>
  <div class="services">
    <div class="service"><div class="dot"><svg width="12" height="12" viewBox="0 0 12 12"><circle cx="5" cy="5" r="3.3" fill="none" stroke="#fff" stroke-width="1.2"/><line x1="7.5" y1="7.5" x2="10.5" y2="10.5" stroke="#fff" stroke-width="1.2"/></svg></div>Research Evaluation</div>
    <div class="service"><div class="dot"><svg width="12" height="12" viewBox="0 0 12 12"><circle cx="6" cy="4" r="2" fill="#fff"/><circle cx="2.5" cy="5" r="1.4" fill="#fff"/><circle cx="9.5" cy="5" r="1.4" fill="#fff"/><path d="M2 11c0-3 8-3 8 0z" fill="#fff"/></svg></div>Community Engagement</div>
    <div class="service"><div class="dot"><svg width="12" height="12" viewBox="0 0 12 12"><rect x="1.5" y="6" width="2" height="4.5" fill="#fff"/><rect x="5" y="3.5" width="2" height="7" fill="#fff"/><rect x="8.5" y="1.5" width="2" height="9" fill="#fff"/></svg></div>On-chain data analysis</div>
  </div>
  <div class="newsletter">
    <svg width="12" height="9" viewBox="0 0 12 9"><rect x="0.6" y="0.6" width="10.8" height="7.8" fill="none" stroke="#149e8e" stroke-width="1"/><path d="M0.6 0.6 6 5 11.4 0.6" fill="none" stroke="#149e8e" stroke-width="1"/></svg>
    <h3>Newsletter Subscribe</h3>
    <p>Get our latest insights in your inbox.</p>
    <div class="subscribe"><span class="field">Your email address</span><span class="btn">Subscribe</span></div>
  </div>
  <footer class="footer" style="height:62px">
    <div class="footer-links"><span>Home</span><span>About Us</span><span>Research</span><span>News</span><span>Contact</span></div>
    <div class="social"><span></span><span></span></div>
    <p class="copy">© 2024 Veltrix Research</p>
  </footer>
</section>

<!-- About page -->
<section class="page about">
  <header class="nav"><span class="logo">Veltrix Research</span>
    <nav class="navlinks"><span>Home</span><span>About Us</span><span>Research</span><span>Careers</span><span>News</span><span>Contact</span></nav>
  </header>
  <div class="hero" style="height:138px" role="img" aria-label="Colourful street-art mural of an elephant on a concrete wall">
    <div class="hero-title" style="top:34px;font-size:15px">Tidewater<br>Digital</div>
    <p class="hero-text" style="top:72px">An independent team focused on research-led investment in emerging blockchain networks.</p>
  </div>
  <h2 style="font-size:10px;margin-top:16px">Our Team</h2>
  <div class="team">
    <div class="member"><div class="portrait" role="img" aria-label="Team member portrait"></div><p class="name">Daniel Brooks</p><p class="role">Founder &amp; CEO</p><p class="bio">Years of experience across markets, technology and protocol research.</p></div>
    <div class="member"><div class="portrait" role="img" aria-label="Team member portrait"></div><p class="name">Owen Hale</p><p class="role">Research Director</p><p class="bio">Years of experience across markets, technology and protocol research.</p></div>
    <div class="member"><div class="portrait" role="img" aria-label="Team member portrait"></div><p class="name">Marcus Reyes</p><p class="role">Lead Analyst</p><p class="bio">Years of experience across markets, technology and protocol research.</p></div>
  </div>
  <footer class="footer" style="height:62px">
    <div class="footer-links"><span>Home</span><span>About Us</span><span>Research</span><span>News</span><span>Contact</span></div>
    <div class="social"><span></span><span></span></div>
    <p class="copy">© 2024 Veltrix Research</p>
  </footer>
</section>

<!-- Careers and contact page -->
<section class="page careers">
  <header class="nav"><span class="logo">Veltrix Research</span>
    <nav class="navlinks"><span>Home</span><span>About Us</span><span>Research</span><span>Careers</span><span>News</span><span>Contact</span></nav>
  </header>
  <div class="hero" style="height:138px" role="img" aria-label="Colourful street-art mural of an elephant on a concrete wall">
    <div class="hero-title" style="top:40px;font-size:17px">Veltrix<br>Research</div>
  </div>
  <div class="job">
    <div class="job-art" role="img" aria-label="Vivid abstract graffiti artwork"></div>
    <div class="job-copy">
      <h3>Careers</h3>
      <p class="sub">Research Analyst</p>
      <p>We are looking for curious analysts who enjoy digging into protocols and writing clear reports.</p>
      <p>Join a small remote team and help shape our research agenda from day one.</p>
    </div>
  </div>
  <div class="contact">
    <h2 style="font-size:10px">Contact Us</h2>
    <p class="lead" style="width:170px;margin-top:3px">Have a question or proposal? Send us a note and we will reply soon.</p>
    <div class="form">
      <span class="input">First name</span><span class="input">Last name</span>
      <span class="input">Email</span><span class="input">Phone</span>
      <span class="input wide">Message</span>
    </div>
    <span class="submit">Submit</span>
  </div>
  <footer class="footer" style="height:60px">
    <div class="footer-links"><span>Home</span><span>About Us</span><span>Research</span><span>News</span><span>Contact</span></div>
    <div class="social"><span></span><span></span></div>
    <p class="copy">© 2024 Veltrix Research</p>
  </footer>
</section>

<!-- Research page -->
<section class="page research">
  <header class="nav"><span class="logo">Veltrix Research</span>
    <nav class="navlinks"><span>Home</span><span>About Us</span><span>Research</span><span>Careers</span><span>News</span><span>Contact</span></nav>
  </header>
  <div class="hero" style="height:138px" role="img" aria-label="Colourful street-art mural of an elephant on a concrete wall">
    <div class="hero-title" style="top:40px;font-size:17px">Veltrix<br>Research</div>
  </div>
  <h2 style="font-size:10px;margin-top:14px">Research-Driven Investing</h2>
  <p class="lead" style="width:240px;margin-top:4px">Our process combines technical review, community signals and on-chain metrics to form a clear view of each project we follow.</p>

  <div class="row" style="top:212px">
    <div class="tech" style="left:0;top:0" role="img" aria-label="Dark teal digital network visual"></div>
    <div class="row-text" style="left:126px;top:22px"><h3>Technology Evaluation</h3><p>We review code quality, team delivery and network design to judge long-term potential.</p></div>
  </div>
  <div class="row" style="top:300px">
    <div class="row-text" style="left:0;top:22px"><h3>Community Engagement</h3><p>We review code quality, team delivery and network design to judge long-term potential.</p></div>
    <div class="tech" style="right:0;top:0" role="img" aria-label="Dark teal digital network visual"></div>
  </div>
  <div class="row" style="top:388px">
    <div class="tech" style="left:0;top:0" role="img" aria-label="Dark teal digital network visual"></div>
    <div class="row-text" style="left:126px;top:22px"><h3>On chain data analysis</h3><p>We review code quality, team delivery and network design to judge long-term potential.</p></div>
  </div>

  <footer class="footer" style="height:66px;background:var(--band)">
    <div class="footer-links"><span>Home</span><span>About Us</span><span>Research</span><span>News</span><span>Contact</span></div>
    <div class="social"><span></span><span></span></div>
    <p class="copy">© 2024 Veltrix Research</p>
  </footer>
</section>

</body>
</html>
```